Business card for my new company (Accounting firm)

I need a business card for my new business Brightwell Advisory and Ledger SA. Our services are accounting, tax, audit and financial management. Our customers are small companies, start-ups and new companies. The final design has to show financial security, trust and growth. Please find our logo attached to the business card. Text for the business card: Brightwell Advisory and Ledger SA Tomas Varenholt Director and Founder Certified Accountant Tel. 022 418 57 34 tv@clairevalconseil.ch www.clairevalconseil.ch Rue des Vergières 27 1201 Geneva
Target Market(s)
Our customers are small companies, start-ups and new companies.
Industry/Entity Type
Finance And Accounting
Contact Information for Business Card
Claireval Conseil et Comptes SA
Tomas Varenholt
Directeur et Fondateur
Expert-comptable diplômé
Tél. 022 418 57 34
tv@clairevalconseil.ch
www.clairevalconseil.ch
Rue des Vergières 27
1201 Genève

```html
<!DOCTYPE html>
<html lang="fr">
<head>
<meta charset="utf-8">
<title>Claireval Conseil et Comptes – Carte de visite</title>
<link href="https://fonts.googleapis.com/css2?family=Roboto:wght@400;500;700&display=swap" rel="stylesheet">
<style>
  :root {
    --page-bg: #d8d5d1;
    --card-bg: #eef0f1;
    --card-edge: #dfe3e5;
    --ink: #2f3235;
    --ink-soft: #3c4044;
    --brand-blue: #1f5f86;
    --brand-square: #2f8fce;
    --band-start: #1b6687;
    --band-end: #2b93b5;
    --band-rule: #3a3f44;
    --band-text: #d7e3e8;
  }
  * { box-sizing: border-box; margin: 0; padding: 0; }
  html, body {
    width: 1200px;
    height: 1054px;
    overflow: hidden;
    background: var(--page-bg);
    font-family: "Roboto", Arial, sans-serif;
  }
  .business-card {
    position: absolute;
    left: 100px;
    top: 227px;
    width: 1000px;
    height: 601px;
    background: var(--card-bg);
    border: 1px solid var(--card-edge);
    box-shadow: 0 10px 30px rgba(0, 0, 0, 0.12);
    overflow: hidden;
  }
  .brand {
    position: absolute;
    left: 70px;
    top: 150px;
    width: 330px;
    display: flex;
    flex-direction: column;
    align-items: center;
    color: var(--ink-soft);
    font-weight: 500;
  }
  .brand-square {
    width: 96px;
    height: 96px;
    background: var(--brand-square);
    margin-bottom: 34px;
  }
  .brand-name {
    font-size: 58px;
    letter-spacing: 4px;
    line-height: 1;
    text-transform: uppercase;
  }
  .brand-tagline {
    margin-top: 12px;
    font-size: 19px;
    letter-spacing: 3px;
    text-transform: uppercase;
  }
  .person {
    position: absolute;
    left: 524px;
    top: 140px;
  }
  .person-name {
    font-size: 37px;
    font-weight: 700;
    color: var(--brand-blue);
    line-height: 1.1;
  }
  .person-roles {
    margin-top: 22px;
    font-size: 21px;
    line-height: 1.45;
    color: var(--ink);
  }
  .contact-list {
    position: absolute;
    left: 537px;
    top: 368px;
    list-style: none;
  }
  .contact-item {
    display: flex;
    align-items: center;
    height: 37px;
    font-size: 24px;
    color: var(--ink);
  }
  .contact-icon {
    width: 22px;
    height: 22px;
    margin-right: 13px;
    fill: var(--ink);
    flex: none;
  }
  .address-rule {
    position: absolute;
    left: 0;
    top: 535px;
    width: 100%;
    height: 3px;
    background: var(--band-rule);
  }
  .address-band {
    position: absolute;
    left: 0;
    top: 542px;
    width: 100%;
    height: 59px;
    background: linear-gradient(90deg, var(--band-start), var(--band-end) 55%, var(--band-start));
    display: flex;
    align-items: center;
    justify-content: center;
    font-size: 23px;
    color: var(--band-text);
  }
</style>
</head>
<body>
  <article class="business-card">
    <div class="brand">
      <div class="brand-square"></div>
      <div class="brand-name">Claireval</div>
      <div class="brand-tagline">Conseil et Comptes</div>
    </div>

    <header class="person">
      <h1 class="person-name">Tomas Varenholt</h1>
      <p class="person-roles">Directeur et Fondateur<br>Expert-comptable diplômé</p>
    </header>

    <ul class="contact-list">
      <li class="contact-item">
        <svg class="contact-icon" viewBox="0 0 24 24" aria-hidden="true">
          <path d="M3 9c0-3 4-5 9-5s9 2 9 5v2h-5V9c0-1-2-1.5-4-1.5S8 8 8 9v2H3z"/>
          <path d="M6 13h12l2 7H4z"/>
        </svg>
        022 418 57 34
      </li>
      <li class="contact-item">
        <svg class="contact-icon" viewBox="0 0 24 24" aria-hidden="true">
          <path d="M2 5h20v14H2z M4 7v1l8 5 8-5V7l-8 5z" fill-rule="evenodd"/>
        </svg>
        tv@clairevalconseil.ch
      </li>
      <li class="contact-item">
        <svg class="contact-icon" viewBox="0 0 24 24" aria-hidden="true">
          <path d="M12 2a10 10 0 1 0 0 20a10 10 0 1 0 0-20zm0 2c1 0 2.3 2 2.8 5H9.2C9.7 6 11 4 12 4zm-3 7h6a17 17 0 0 1 0 2H9a17 17 0 0 1 0-2zm-5 0h3a19 19 0 0 0 0 2H4a8 8 0 0 1 0-2zm13 0h3a8 8 0 0 1 0 2h-3a19 19 0 0 0 0-2zM9.2 15h5.6c-.5 3-1.8 5-2.8 5s-2.3-2-2.8-5z"/>
        </svg>
        www.clairevalconseil.ch
      </li>
    </ul>

    <div class="address-rule"></div>
    <footer class="address-band">Rue des Vergières 27 1201 Genève</footer>
  </article>
</body>
</html>
```